Moulding supply company needs a Door Hanger Design

Door Hanger Design Request from Loft Crafta
www. loftcraftas.ca
We are moulding factory outlet in Toronto. Provide high quality moulding materials with competitive price like crown mouldings, casings, wainscoting, flatstocks, baseboards. We also provide professional installation for our clients. This door hanger will help the home owner easily find a local factory supplier with providing the materials as well as installation.

Detail request for design:
Size: 4”x11”, vertical
Shape: Rectangle

Content:
Front
1. Logo, see attachment(Use the left one, horizontal one)
2. Moulding factory outlet direct sale
3. Supply high quality Crown mouldings, baseboards, casings and wainscotings with competitive price
4. Installation & delivery
#2 content is the most important content, should be bold and readable
#3 can be smaller font compare to #2

Address: 47 West Falcon Ridge Rd, Richmond Hill, ON L3K 2P9
Telephone: 416 730 4215
416 682 1947
Email: info@loftcraftas.ca

Back
Slogan: Convert plain room into designer’s interiors

Telephone: 416 730 4215
416 682 1947
Email: info@loftcraftas.ca

Images:
Front
1. Display our productions for crown mouldings, baseboards, casings and wainscotings, refer to our website www.loftcraftas.ca. (The winner finally we will provide the high resolution images, low resolution please copy from our website so far)
Back
2. Display 4-6 nice images for 1. wainscoting walls 2. feature walls, 3. waffle ceiling like attached below. BUT PLEASE DON'T USE THE IMAGES PROVIDED, THIS IS ONLY A SAMPLE. Please use high resolution images for printing. ALSO PLEASE DON'T LIMIT YOUR CREATIVITY TO USE 4 SQUARES LIKE BELOW IMAGES. Please provide more ideas

Note:
1. Please do the bleeding for final printing production
2. Images have to be high resolution for ready to print
3. Style need to be fresh, clean, easy to read, modern and magazine style
4. Information has to be readable, easy to find, front and back both need to display company address, telephone, email, you can use icon or abbreviation to do these information.

Thanks,
Loft Craftas

```html
<!DOCTYPE html>
<html lang="en">
<head>
<meta charset="utf-8">
<title>Loft Craftas – Door Hangers</title>
<link rel="stylesheet" href="https://fonts.googleapis.com/css2?family=Bebas+Neue&family=Lato:wght@400;700&family=Quicksand:wght@400;500;600;700&display=swap">
<style>
  :root {
    --stage: #262626;
    --paper: #ffffff;
    --orange: #ee5a2a;
    --blue: #2451a3;
    --ink: #2f2f2f;
    --grey: #6d6e71;
  }
  * { margin: 0; padding: 0; box-sizing: border-box; }
  html, body { width: 1200px; height: 1092px; overflow: hidden; background: var(--stage); }
  .canvas { position: relative; width: 1200px; height: 1092px; }

  .hanger {
    position: absolute; top: 89px; width: 331px; height: 913px;
    background: var(--paper); overflow: hidden;
    font-family: "Quicksand", sans-serif;
  }
  .hanger--front { left: 234px; }
  .hanger--back { left: 634px; }

  .hanger__cutout { position: absolute; left: 0; top: 0; width: 331px; height: 190px; z-index: 5; pointer-events: none; }

  .brand { position: absolute; left: 0; width: 100%; display: flex; justify-content: center; align-items: center; gap: 8px; }
  .brand__square { width: 12px; height: 12px; background: var(--orange); }
  .brand__name { font-family: "Quicksand", sans-serif; font-weight: 700; font-size: 22px; color: var(--ink); line-height: 1; }

  /* front */
  .front-photo { position: absolute; left: 0; top: 262px; width: 331px; height: 248px; }
  .headline {
    position: absolute; left: 0; top: 526px; width: 100%; text-align: center;
    font-family: "Bebas Neue", sans-serif; font-weight: 400; font-size: 40px; line-height: 36px; color: var(--orange); letter-spacing: 0.5px;
  }
  .headline-rule { position: absolute; left: 105px; top: 608px; width: 121px; height: 2px; background: var(--ink); }
  .lead {
    position: absolute; left: 42px; top: 617px; width: 247px; text-align: center;
    font-size: 12.5px; line-height: 15px; color: var(--grey); font-weight: 400;
  }
  .product-hexes { position: absolute; left: 0; top: 668px; width: 331px; height: 132px; }
  .services {
    position: absolute; left: 0; top: 800px; width: 100%; text-align: center;
    font-weight: 700; font-size: 19px; color: var(--blue);
  }
  .front-footer {
    position: absolute; left: 0; bottom: 0; width: 100%; height: 67px;
    background: var(--blue); border-top: 3px solid var(--orange);
    padding-top: 8px; text-align: center;
    font-family: "Lato", sans-serif; font-size: 10.5px; line-height: 17px; color: #fff;
  }

  /* back */
  .back-photo { position: absolute; left: 0; top: 0; width: 331px; height: 385px; }
  .back-band { position: absolute; left: 0; top: 385px; width: 100%; height: 7px; background: var(--blue); }
  .slogan {
    position: absolute; left: 0; top: 526px; width: 100%; text-align: center;
    font-size: 20px; line-height: 24px; color: var(--orange); font-weight: 500;
  }
  .back-gallery { position: absolute; left: 0; top: 610px; width: 331px; height: 188px; }
  .back-contact {
    position: absolute; left: 0; top: 850px; width: 100%; text-align: center; font-style: normal;
    font-family: "Lato", sans-serif; font-size: 10.5px; line-height: 17px; color: var(--ink);
  }
  .back-base { position: absolute; left: 0; bottom: 0; width: 100%; height: 6px; background: var(--blue); }
</style>
</head>
<body>
<div class="canvas">

  <!-- Front -->
  <section class="hanger hanger--front">
    <div class="brand" style="top:215px">
      <span class="brand__square"></span><span class="brand__name">Loft Craftas</span>
    </div>

    <svg class="front-photo" viewBox="0 0 331 248">
      <defs>
        <linearGradient id="factoryTones" x1="0" y1="0" x2="0" y2="1">
          <stop offset="0" stop-color="#9a9486"/>
          <stop offset="0.35" stop-color="#c9a24a"/>
          <stop offset="0.6" stop-color="#777c80"/>
          <stop offset="1" stop-color="#2f6b55"/>
        </linearGradient>
      </defs>
      <g role="img" aria-label="Photo of a large moulding factory hall with overhead cranes and a green floor aisle">
        <path d="M0 12 H148 L174 38 H331 V208 H0 Z" fill="url(#factoryTones)"/>
      </g>
      <path d="M0 7 H144 Q150 7 154 11 L176 32 H331" fill="none" stroke="var(--orange)" stroke-width="9"/>
      <path d="M0 210 H75 Q79 210 83 214 L101 232 Q104 235 110 235 H331 V246 H104 Q98 246 94 242 L76 224 Q73 221 68 221 H0 Z" fill="var(--orange)"/>
      <path d="M0 221 H68 Q73 221 76 224 L94 242 Q98 246 104 246 H331 V248 H0 Z" fill="var(--paper)"/>
    </svg>

    <h1 class="headline">MOULDING FACTORY<br>OUTLET DIRECT SALE</h1>
    <div class="headline-rule"></div>
    <p class="lead">Supply high quality Crown mouldings, baseboards, casings and wainscotings with competitive Price.</p>

    <svg class="product-hexes" viewBox="0 0 331 132">
      <defs>
        <linearGradient id="wainscotTone" x1="0" y1="0" x2="1" y2="1"><stop offset="0" stop-color="#d8d0c7"/><stop offset="1" stop-color="#a89d92"/></linearGradient>
        <linearGradient id="crownTone" x1="0" y1="0" x2="1" y2="1"><stop offset="0" stop-color="#2a2a2a"/><stop offset="0.5" stop-color="#e9e9e9"/><stop offset="1" stop-color="#cfcfcf"/></linearGradient>
        <linearGradient id="baseTone" x1="0" y1="0" x2="0" y2="1"><stop offset="0" stop-color="#e8e2cf"/><stop offset="0.6" stop-color="#d9cfb5"/><stop offset="1" stop-color="#a9773f"/></linearGradient>
      </defs>
      <polygon role="img" aria-label="Wainscoting wall panel product photo" points="62,26 95,45 95,86 62,105 29,86 29,45" fill="url(#wainscotTone)" stroke="var(--orange)" stroke-width="3.5"/>
      <polygon role="img" aria-label="White crown moulding product photo" points="164,6 217,36 217,97 164,127 111,97 111,36" fill="url(#crownTone)" stroke="var(--orange)" stroke-width="4"/>
      <polygon role="img" aria-label="Baseboard and casing product photo" points="267,26 300,45 300,86 267,105 234,86 234,45" fill="url(#baseTone)" stroke="var(--orange)" stroke-width="3.5"/>
    </svg>

    <p class="services">Installation &amp; Delivery</p>

    <footer class="front-footer">
      416 730 4215, 416 682 1947<br>
      47 West Falcon Ridge Rd, Richmond Hill, ON L3K 2P9<br>
      info@loftcraftas.ca
    </footer>

    <svg class="hanger__cutout" viewBox="0 0 331 190">
      <path d="M0 96 H93 Q100 96 102 90 A70 70 0 1 1 102 124 Q100 117 93 117 H0 Z" fill="var(--stage)"/>
    </svg>
  </section>

  <!-- Back -->
  <section class="hanger hanger--back">
    <svg class="back-photo" viewBox="0 0 331 385">
      <defs>
        <linearGradient id="hallTones" x1="0" y1="0" x2="0" y2="1">
          <stop offset="0" stop-color="#a49f93"/>
          <stop offset="0.3" stop-color="#c9a24a"/>
          <stop offset="0.6" stop-color="#7b8185"/>
          <stop offset="1" stop-color="#2e6a55"/>
        </linearGradient>
      </defs>
      <rect role="img" aria-label="Photo of the moulding factory production hall" width="331" height="385" fill="url(#hallTones)"/>
      <polygon points="228,0 331,0 331,143 198,385 0,385 0,280" fill="var(--orange)" opacity="0.72"/>
    </svg>
    <div class="back-band"></div>

    <div class="brand" style="top:467px">
      <span class="brand__square"></span><span class="brand__name">Loft Craftas</span>
    </div>

    <p class="slogan">Convert plain room into<br>designer’s interiors</p>

    <svg class="back-gallery" viewBox="0 0 331 188">
      <defs>
        <linearGradient id="crownPhoto" x1="0" y1="0" x2="1" y2="1"><stop offset="0" stop-color="#3a3a3a"/><stop offset="0.45" stop-color="#ececec"/><stop offset="1" stop-color="#bdbdbd"/></linearGradient>
        <linearGradient id="basePhoto" x1="0" y1="0" x2="0" y2="1"><stop offset="0" stop-color="#3c4252"/><stop offset="0.45" stop-color="#ebe4cf"/><stop offset="1" stop-color="#b0783c"/></linearGradient>
      </defs>
      <rect x="0" y="0" width="331" height="5" fill="var(--orange)"/>
      <rect x="0" y="182" width="331" height="5" fill="var(--orange)"/>
      <polygon role="img" aria-label="Close-up photo of white crown moulding at a ceiling corner" points="0,5 188,5 128,182 0,182" fill="url(#crownPhoto)"/>
      <polygon role="img" aria-label="Photo of cream baseboard and door casing on a wood floor" points="196,5 331,5 331,182 136,182" fill="url(#basePhoto)"/>
      <polygon points="188,0 196,0 136,188 128,188" fill="var(--paper)"/>
    </svg>

    <address class="back-contact">
      416 730 4215, 416 682 1947<br>
      47 West Falcon Ridge Rd, Richmond Hill, ON L3K 2P9<br>
      info@loftcraftas.ca
    </address>
    <div class="back-base"></div>

    <svg class="hanger__cutout" viewBox="0 0 331 190">
      <path d="M0 96 H93 Q100 96 102 90 A70 70 0 1 1 102 124 Q100 117 93 117 H0 Z" fill="var(--stage)"/>
    </svg>
  </section>

</div>
</body>
</html>
```